Maple Roster Business Card for recruitment company

We are looking for a Business Card Design that incorporates our personal details and our busines name and logo. We are a specialized search consultancy that recruit Property and Construction professionals.
We would like a business card that stands out and is appealing to the Construction and Property industry as well.

Target Market(s)

people in the construction and property industry

Contact Information for Business Card

Business Name and logo

Font styles to use
Serif

Colors
0094D4
00A9DD
6FCCEA
C7EBF8
E9F6FB

Requirements
Must have
• Business name and logo as well as contact details
Should not have
• No photos of us please

```html
<!DOCTYPE html>
<html lang="en">
<head>
<meta charset="utf-8">
<title>Maple Roster Business Card</title>
<link rel="stylesheet" href="https://fonts.googleapis.com/css2?family=Montserrat:wght@300;400;500;700&display=swap">
<style>
  :root {
    --stage: #2a2d31;
    --card: #0d4660;
    --card-deep: #0a3a50;
    --accent: #f07a1a;
    --ink: #ffffff;
    --ink-soft: #d7e4ea;
  }
  * { box-sizing: border-box; margin: 0; padding: 0; }
  html, body { width: 1200px; height: 780px; overflow: hidden; }
  body {
    background: var(--stage);
    font-family: "Montserrat", sans-serif;
    display: flex;
    align-items: center;
    justify-content: center;
    gap: 40px;
  }
  .card {
    position: relative;
    width: 540px;
    height: 310px;
    border-radius: 18px;
    background: var(--card);
    overflow: hidden;
  }
  .card-front .brand {
    position: absolute;
    left: 34px;
    top: 66px;
    font-weight: 300;
    font-size: 26px;
    letter-spacing: 1px;
    text-transform: uppercase;
    white-space: nowrap;
    color: var(--ink);
  }
  .card-front .divider {
    position: absolute;
    left: 0; top: 0;
    width: 540px; height: 310px;
  }
  .person {
    position: absolute;
    left: 326px;
    top: 46px;
  }
  .person-name {
    font-weight: 700;
    font-size: 21px;
    letter-spacing: 1px;
    color: var(--accent);
    white-space: nowrap;
  }
  .person-title {
    margin-top: 2px;
    font-weight: 400;
    font-size: 11px;
    letter-spacing: 1.2px;
    color: var(--ink);
  }
  .contact {
    position: absolute;
    left: 292px;
    top: 150px;
    list-style: none;
  }
  .contact li {
    display: flex;
    align-items: flex-start;
    gap: 10px;
    font-weight: 500;
    font-size: 12px;
    letter-spacing: 1px;
    line-height: 16px;
    color: var(--ink);
    margin-bottom: 10px;
    white-space: nowrap;
  }
  .contact svg { flex: none; width: 14px; height: 14px; margin-top: 1px; }
  .card-back .pattern {
    position: absolute;
    inset: 0;
    background: linear-gradient(135deg, #0f5570 0%, var(--card) 50%, var(--card-deep) 100%);
  }
  .card-back .back-brand {
    position: absolute;
    left: 0; right: 0;
    top: 200px;
    display: flex;
    align-items: center;
    justify-content: center;
    gap: 10px;
    font-weight: 300;
    font-size: 20px;
    letter-spacing: 1px;
    text-transform: uppercase;
    color: var(--accent);
  }
  .back-brand .dot {
    width: 14px; height: 14px;
    border-radius: 50%;
    background: var(--accent);
  }
</style>
</head>
<body>
  <section class="card card-front">
    <div class="brand">Maple Roster</div>
    <svg class="divider" viewBox="0 0 540 310" aria-hidden="true">
      <line x1="312" y1="26" x2="232" y2="290" stroke="#f07a1a" stroke-width="1.5"/>
    </svg>
    <div class="person">
      <div class="person-name">Idris Kellan</div>
      <div class="person-title">General Manager</div>
    </div>
    <ul class="contact">
      <li>
        <svg viewBox="0 0 16 16" fill="none" stroke="#f07a1a" stroke-width="1.3"><path d="M4 2l2.5 3-1.5 1.5c.8 1.8 2.2 3.2 4 4L10.5 9 13.5 11.5 12 14C7 13.5 2.5 9 2 4z"/></svg>
        041-552-7394
      </li>
      <li>
        <svg viewBox="0 0 16 16" fill="none" stroke="#f07a1a" stroke-width="1.3"><rect x="2" y="4" width="12" height="9"/><path d="M2 4l6 5 6-5"/></svg>
        hello@mapleroster.com
      </li>
      <li>
        <svg viewBox="0 0 16 16" fill="none" stroke="#f07a1a" stroke-width="1.3"><circle cx="8" cy="8" r="6"/><path d="M2 8h12M8 2c2.5 3 2.5 9 0 12M8 2c-2.5 3-2.5 9 0 12"/></svg>
        www.mapleroster.com
      </li>
      <li>
        <svg viewBox="0 0 16 16" fill="none" stroke="#f07a1a" stroke-width="1.3"><path d="M8 14s-4.5-4.5-4.5-7.5a4.5 4.5 0 0 1 9 0C12.5 9.5 8 14 8 14z"/><circle cx="8" cy="6.5" r="1.6"/></svg>
        <span>4820 Cedar Row Lane<br>Alden, VA 20417</span>
      </li>
    </ul>
  </section>

  <section class="card card-back">
    <div class="pattern" role="img" aria-label="Repeating brand mark pattern in tonal teal"></div>
    <div class="back-brand"><span class="dot"></span>Maple Roster</div>
  </section>
</body>
</html>
```